1/4 page ad for Brightmoor magazine

Placing an ad in the Brightmoor Canada magazine.
3.475 (w) x 4.75 (h)
Please design in Adobe Illustrator and provide original file.
Logo attached.
Prior brochure attached.
Please include website and contact info.

```html
<!DOCTYPE html>
<html lang="en">
<head>
<meta charset="utf-8">
<title>Clarova – quarter page ad options</title>
<link href="https://fonts.googleapis.com/css2?family=Exo+2:wght@800&family=Oswald:wght@400&family=Montserrat:wght@600;700&display=swap" rel="stylesheet">
<style>
  :root{
    --green:#4a8c3c;
    --black:#000;
    --white:#fff;
    --backdrop:#e6e6e6;
    --unit-light:#eceeef;
    --unit-dark:#b9bec2;
  }
  html,body{margin:0;padding:0;width:1072px;height:1200px;overflow:hidden;background:var(--backdrop);}
  .sheet{position:absolute;left:0;top:0;width:1200px;height:1343px;transform:scale(0.89333);transform-origin:0 0;}
  .ad{position:absolute;width:413px;height:564px;overflow:hidden;background:var(--white);color:var(--green);}
  .ad--a{left:150px;top:83px;}
  .ad--b{left:637px;top:83px;}
  .ad--c{left:150px;top:696px;}
  .ad--d{left:637px;top:696px;background:var(--black);color:var(--white);}
  .ad__shapes{position:absolute;inset:0;width:413px;height:564px;}
  .brand{position:absolute;left:18px;top:22px;width:120px;text-align:center;}
  .brand__mark{display:block;width:73px;height:65px;margin:0 auto;border-radius:12px;background:var(--green);}
  .brand__name{display:block;margin-top:4px;font-family:"Exo 2",sans-serif;font-weight:800;font-size:28px;letter-spacing:0.5px;color:var(--green);}
  .ad--c .brand__mark,.ad--d .brand__mark{background:var(--white);}
  .ad--c .brand__name,.ad--d .brand__name{color:var(--white);}
  .ad--b .brand,.ad--d .brand{top:37px;left:24px;}
  .headline{position:absolute;left:170px;top:18px;margin:0;font-family:"Exo 2",sans-serif;font-weight:800;font-size:23.5px;line-height:27px;text-transform:uppercase;color:var(--green);white-space:nowrap;}
  .ad--b .headline,.ad--d .headline{left:164px;top:32px;}
  .ad--c .headline,.ad--d .headline{color:var(--white);}
  .features{position:absolute;left:192px;top:153px;margin:0;padding:0;list-style:none;font-family:"Oswald",sans-serif;font-size:15px;line-height:21px;width:218px;white-space:nowrap;}
  .ad--b .features,.ad--d .features{left:186px;}
  .ad--c .features{top:163px;}
  .features li{position:relative;padding-left:16px;}
  .features li + li{margin-top:12px;}
  .features li.features__last{margin-top:18px;}
  .features li::before{content:"";position:absolute;left:2px;top:8px;border-left:6px solid currentColor;border-top:3.5px solid transparent;border-bottom:3.5px solid transparent;}
  .product{position:absolute;left:18px;top:172px;width:150px;height:290px;background:linear-gradient(90deg,var(--unit-light) 0%,var(--white) 45%,var(--unit-dark) 100%);border-radius:3px;}
  .ad--b .product{left:16px;}
  .ad--c .product{top:186px;}
  .ad--d .product{left:16px;top:170px;}
  .contact{position:absolute;right:17px;top:470px;text-align:right;color:var(--white);font-family:"Montserrat",sans-serif;}
  .ad--b .contact,.ad--d .contact{right:33px;top:478px;}
  .contact__cta{margin:0;font-weight:600;font-size:14px;letter-spacing:1px;}
  .contact__phone{margin:6px 0 0;font-weight:700;font-size:21px;display:flex;align-items:center;justify-content:flex-end;gap:8px;}
  .footer{position:absolute;left:18px;right:17px;top:532px;display:flex;justify-content:space-between;font-family:"Montserrat",sans-serif;font-weight:700;font-size:11.5px;color:var(--white);}
  .ad--b .footer,.ad--d .footer{left:32px;right:36px;top:533px;}
  .footer span{display:flex;align-items:center;gap:5px;}
  .icon{display:block;}
</style>
</head>
<body>
<div class="sheet">

  <!-- Variant A: white with angled green base -->
  <section class="ad ad--a">
    <svg class="ad__shapes" viewBox="0 0 413 564" aria-hidden="true">
      <polygon fill="var(--green)" points="0,465 85,504 220,452 413,452 413,564 0,564"/>
    </svg>
    <div class="brand"><span class="brand__mark"></span><span class="brand__name">clarova</span></div>
    <h2 class="headline">Disinfection,<br>decontamination,<br>and aeration all<br>in one product</h2>
    <ul class="features">
      <li>Faster and more effective<br>than alternatives<br>(e.g. chlorine, UV, RO etc.)</li>
      <li>No chemicals added or left behind</li>
      <li>Supersaturates water with oxygen</li>
      <li class="features__last">Ideal for treating recirculated<br>water, reservoirs, irrigation lines,<br>drains, and sumps</li>
    </ul>
    <div class="product" role="img" aria-label="Photo of a freestanding ozone generator cabinet with pipework"></div>
    <div class="contact">
      <p class="contact__cta">CALL US ANYTIME!</p>
      <p class="contact__phone"><svg class="icon" width="24" height="24" viewBox="0 0 24 24"><circle cx="12" cy="12" r="12" fill="var(--white)"/><path d="M8 6l2 0 1.2 3-1.6 1.2a8 8 0 0 0 4.2 4.2L15 12.8l3 1.2v2a2 2 0 0 1-2 2A10 10 0 0 1 6 8a2 2 0 0 1 2-2z" fill="var(--green)"/></svg>1-888-555-0147</p>
    </div>
    <div class="footer">
      <span><svg class="icon" width="13" height="13" viewBox="0 0 14 14"><g fill="none" stroke="var(--white)" stroke-width="1.3"><circle cx="7" cy="7" r="6"/><ellipse cx="7" cy="7" rx="2.6" ry="6"/><path d="M1 7h12"/></g></svg>www.clarova-water.com</span>
      <span><svg class="icon" width="13" height="13" viewBox="0 0 14 14"><circle cx="7" cy="7" r="7" fill="var(--white)"/><path d="M3.5 5h7v4.5h-7z M3.5 5l3.5 2.5L10.5 5" fill="none" stroke="var(--green)" stroke-width="1.1"/></svg>info@clarova-water.com</span>
    </div>
  </section>

  <!-- Variant B: white with curved green corners -->
  <section class="ad ad--b">
    <svg class="ad__shapes" viewBox="0 0 413 564" aria-hidden="true">
      <path fill="var(--green)" d="M300,0 C385,0 408,40 413,115 L413,0 Z"/>
      <path fill="var(--green)" d="M0,478 L85,506 L290,455 C375,440 408,480 413,564 L0,564 Z"/>
    </svg>
    <div class="brand"><span class="brand__mark"></span><span class="brand__name">clarova</span></div>
    <h2 class="headline">Disinfection,<br>decontamination,<br>and aeration all<br>in one product</h2>
    <ul class="features">
      <li>Faster and more effective<br>than alternatives<br>(e.g. chlorine, UV, RO etc.)</li>
      <li>No chemicals added or left behind</li>
      <li>Supersaturates water with oxygen</li>
      <li class="features__last">Ideal for treating recirculated<br>water, reservoirs, irrigation lines,<br>drains, and sumps</li>
    </ul>
    <div class="product" role="img" aria-label="Photo of a freestanding ozone generator cabinet with pipework"></div>
    <div class="contact">
      <p class="contact__cta">CALL US ANYTIME!</p>
      <p class="contact__phone"><svg class="icon" width="24" height="24" viewBox="0 0 24 24"><circle cx="12" cy="12" r="12" fill="var(--white)"/><path d="M8 6l2 0 1.2 3-1.6 1.2a8 8 0 0 0 4.2 4.2L15 12.8l3 1.2v2a2 2 0 0 1-2 2A10 10 0 0 1 6 8a2 2 0 0 1 2-2z" fill="var(--green)"/></svg>1-888-555-0147</p>
    </div>
    <div class="footer">
      <span><svg class="icon" width="13" height="13" viewBox="0 0 14 14"><g fill="none" stroke="var(--white)" stroke-width="1.3"><circle cx="7" cy="7" r="6"/><ellipse cx="7" cy="7" rx="2.6" ry="6"/><path d="M1 7h12"/></g></svg>www.clarova-water.com</span>
      <span><svg class="icon" width="13" height="13" viewBox="0 0 14 14"><circle cx="7" cy="7" r="7" fill="var(--white)"/><path d="M3.5 5h7v4.5h-7z M3.5 5l3.5 2.5L10.5 5" fill="none" stroke="var(--green)" stroke-width="1.1"/></svg>info@clarova-water.com</span>
    </div>
  </section>

  <!-- Variant C: green header band -->
  <section class="ad ad--c">
    <svg class="ad__shapes" viewBox="0 0 413 564" aria-hidden="true">
      <polygon fill="var(--green)" points="0,0 413,0 413,129 0,159"/>
      <polygon fill="var(--green)" points="0,465 85,504 220,460 413,460 413,564 0,564"/>
    </svg>
    <div class="brand"><span class="brand__mark"></span><span class="brand__name">clarova</span></div>
    <h2 class="headline">Disinfection,<br>decontamination,<br>and aeration all<br>in one product</h2>
    <ul class="features">
      <li>Faster and more effective<br>than alternatives<br>(e.g. chlorine, UV, RO etc.)</li>
      <li>No chemicals added or left behind</li>
      <li>Supersaturates water with oxygen</li>
      <li class="features__last">Ideal for treating recirculated<br>water, reservoirs, irrigation lines,<br>drains, and sumps</li>
    </ul>
    <div class="product" role="img" aria-label="Photo of a freestanding ozone generator cabinet with pipework"></div>
    <div class="contact">
      <p class="contact__cta">CALL US ANYTIME!</p>
      <p class="contact__phone"><svg class="icon" width="24" height="24" viewBox="0 0 24 24"><circle cx="12" cy="12" r="12" fill="var(--white)"/><path d="M8 6l2 0 1.2 3-1.6 1.2a8 8 0 0 0 4.2 4.2L15 12.8l3 1.2v2a2 2 0 0 1-2 2A10 10 0 0 1 6 8a2 2 0 0 1 2-2z" fill="var(--green)"/></svg>1-888-555-0147</p>
    </div>
    <div class="footer">
      <span><svg class="icon" width="13" height="13" viewBox="0 0 14 14"><g fill="none" stroke="var(--white)" stroke-width="1.3"><circle cx="7" cy="7" r="6"/><ellipse cx="7" cy="7" rx="2.6" ry="6"/><path d="M1 7h12"/></g></svg>www.clarova-water.com</span>
      <span><svg class="icon" width="13" height="13" viewBox="0 0 14 14"><circle cx="7" cy="7" r="7" fill="var(--white)"/><path d="M3.5 5h7v4.5h-7z M3.5 5l3.5 2.5L10.5 5" fill="none" stroke="var(--green)" stroke-width="1.1"/></svg>info@clarova-water.com</span>
    </div>
  </section>

  <!-- Variant D: black with curved corners -->
  <section class="ad ad--d">
    <svg class="ad__shapes" viewBox="0 0 413 564" aria-hidden="true">
      <path fill="var(--backdrop)" d="M300,-1 C385,-1 408,40 414,115 L414,-1 Z"/>
    </svg>
    <div class="brand"><span class="brand__mark"></span><span class="brand__name">clarova</span></div>
    <h2 class="headline">Disinfection,<br>decontamination,<br>and aeration all<br>in one product</h2>
    <ul class="features">
      <li>Faster and more effective<br>than alternatives<br>(e.g. chlorine, UV, RO etc.)</li>
      <li>No chemicals added or left behind</li>
      <li>Supersaturates water with oxygen</li>
      <li class="features__last">Ideal for treating recirculated<br>water, reservoirs, irrigation lines,<br>drains, and sumps</li>
    </ul>
    <div class="product" role="img" aria-label="Photo of a freestanding ozone generator cabinet with pipework"></div>
    <div class="contact">
      <p class="contact__cta">CALL US ANYTIME!</p>
      <p class="contact__phone"><svg class="icon" width="24" height="24" viewBox="0 0 24 24"><circle cx="12" cy="12" r="12" fill="var(--white)"/><path d="M8 6l2 0 1.2 3-1.6 1.2a8 8 0 0 0 4.2 4.2L15 12.8l3 1.2v2a2 2 0 0 1-2 2A10 10 0 0 1 6 8a2 2 0 0 1 2-2z" fill="var(--black)"/></svg>1-888-555-0147</p>
    </div>
    <div class="footer">
      <span><svg class="icon" width="13" height="13" viewBox="0 0 14 14"><g fill="none" stroke="var(--white)" stroke-width="1.3"><circle cx="7" cy="7" r="6"/><ellipse cx="7" cy="7" rx="2.6" ry="6"/><path d="M1 7h12"/></g></svg>www.clarova-water.com</span>
      <span><svg class="icon" width="13" height="13" viewBox="0 0 14 14"><circle cx="7" cy="7" r="7" fill="var(--white)"/><path d="M3.5 5h7v4.5h-7z M3.5 5l3.5 2.5L10.5 5" fill="none" stroke="var(--black)" stroke-width="1.1"/></svg>info@clarova-water.com</span>
    </div>
  </section>

</div>
</body>
</html>
```